design a construction company business card

Design business card around our logo. Card must have all the typical info: name, title, address, phone, email, business name, etc. Somewhere on the card I would like to see our motto "Built with purpose... Driven by craftsmanship." Consider adding a splash of bright orange to the card to complement the blues and silvers/grays in the logo. We are open to metallic inks, textures, etc. We would like to see options on both light and dark backgrounds. The font in the logo is Euro Technic Extended Regular.

```html
<!DOCTYPE html>
<html lang="en">
<head>
<meta charset="UTF-8">
<title>Halvern Contracting – Business Card</title>
<link rel="stylesheet" href="https://fonts.googleapis.com/css2?family=Michroma&family=Exo+2:wght@400;500&display=swap">
<style>
  :root {
    --backdrop: #8c8c8e;
    --card: #1b1b1d;
    --card-edge: #232326;
    --brand-blue: #2a6fd6;
    --accent-blue: #1f86e0;
    --text-light: #c9cacd;
    --text-muted: #a7a8ab;
  }
  * { margin: 0; padding: 0; box-sizing: border-box; }
  html, body { width: 1200px; height: 1000px; overflow: hidden; }
  body {
    background: radial-gradient(ellipse at 50% 40%, #9a9a9c 0%, var(--backdrop) 60%, #6f6f72 100%);
    font-family: "Exo 2", sans-serif;
    position: relative;
  }
  .card {
    position: absolute;
    left: 250px;
    width: 700px;
    height: 400px;
    border-radius: 26px;
    background: linear-gradient(135deg, var(--card-edge) 0%, var(--card) 55%, #151517 100%);
    box-shadow: 0 18px 40px rgba(0,0,0,0.35);
    overflow: hidden;
  }
  .card--front { top: 60px; }
  .card--back { top: 540px; }

  .wordmark {
    font-family: "Michroma", sans-serif;
    color: var(--brand-blue);
    font-weight: 400;
    text-align: center;
    display: flex;
    align-items: center;
    gap: 18px;
  }
  .wordmark__square {
    width: 22px; height: 22px;
    background: var(--brand-blue);
    flex-shrink: 0;
  }
  .wordmark__name { display: block; letter-spacing: 4px; line-height: 1; }
  .wordmark__sub { display: block; letter-spacing: 2px; margin-top: 12px; }

  .card--front .wordmark {
    position: absolute;
    left: 0; right: 0; top: 120px;
    justify-content: center;
  }
  .card--front .wordmark__name { font-size: 56px; }
  .card--front .wordmark__sub { font-size: 17px; }

  .motto {
    position: absolute;
    left: 0; right: 0; top: 292px;
    text-align: center;
    font-family: "Michroma", sans-serif;
    font-size: 13px;
    letter-spacing: 1px;
    color: var(--accent-blue);
  }

  .card--back .wordmark {
    position: absolute;
    right: 50px; top: 150px;
  }
  .card--back .wordmark__square { width: 20px; height: 20px; }
  .card--back .wordmark__name { font-size: 40px; }
  .card--back .wordmark__sub { font-size: 13px; }

  .contact {
    position: absolute;
    left: 0; top: 120px;
  }
  .contact__bar {
    position: absolute;
    left: 0; top: 4px;
    width: 8px; height: 34px;
    background: var(--accent-blue);
  }
  .contact__name {
    margin-left: 40px;
    font-family: "Michroma", sans-serif;
    font-size: 20px;
    font-weight: 400;
    color: var(--accent-blue);
    letter-spacing: 1px;
  }
  .contact__title {
    margin-left: 40px;
    margin-top: 4px;
    font-size: 17px;
    color: var(--text-muted);
  }
  .contact__address {
    margin-left: 40px;
    margin-top: 18px;
    font-size: 17px;
    line-height: 1.3;
    color: var(--text-muted);
  }
  .contact__list {
    list-style: none;
    margin-left: 40px;
    margin-top: 12px;
  }
  .contact__item {
    display: flex;
    align-items: center;
    gap: 10px;
    font-size: 17px;
    color: var(--text-light);
    line-height: 1.55;
  }
  .contact__icon { width: 14px; height: 14px; flex-shrink: 0; }
  .contact__highlight { color: var(--accent-blue); }
</style>
</head>
<body>

  <section class="card card--front" aria-label="Business card front">
    <div class="wordmark">
      <span class="wordmark__square"></span>
      <div>
        <span class="wordmark__name">HALVERN</span>
        <span class="wordmark__sub">CONTRACTING, INC.</span>
      </div>
    </div>
    <p class="motto">BUILT WITH PURPOSE... DRIVEN BY CRAFTSMANSHIP.</p>
  </section>

  <section class="card card--back" aria-label="Business card back">
    <div class="contact">
      <span class="contact__bar"></span>
      <h1 class="contact__name">Marcus Hale</h1>
      <p class="contact__title">Managing Director</p>
      <p class="contact__address">4870 Westbrook Avenue<br>Ridgefield CT 06877</p>
      <ul class="contact__list">
        <li class="contact__item">
          <svg class="contact__icon" viewBox="0 0 16 16" aria-hidden="true"><path fill="#1f86e0" d="M3.5 1.5l2.5 0 1 3.5-1.6 1.2c.8 1.7 2.2 3.1 3.9 3.9l1.2-1.6 3.5 1v2.5c0 .8-.7 1.5-1.5 1.5C6.7 13.5 2 8.8 2 3c0-.8.7-1.5 1.5-1.5z"/></svg>
          555.014.2280
        </li>
        <li class="contact__item">
          <svg class="contact__icon" viewBox="0 0 16 16" aria-hidden="true"><rect x="1.5" y="3.5" width="13" height="9" rx="1" fill="none" stroke="#1f86e0" stroke-width="1.6"/><path d="M2 4l6 5 6-5" fill="none" stroke="#1f86e0" stroke-width="1.6"/></svg>
          marcus@halverncontract.com
        </li>
        <li class="contact__item">
          <svg class="contact__icon" viewBox="0 0 16 16" aria-hidden="true"><circle cx="8" cy="8" r="6.5" fill="none" stroke="#1f86e0" stroke-width="1.4"/><ellipse cx="8" cy="8" rx="2.8" ry="6.5" fill="none" stroke="#1f86e0" stroke-width="1.2"/><path d="M1.5 8h13" stroke="#1f86e0" stroke-width="1.2"/></svg>
          <span>www.<span class="contact__highlight">halverncontract</span>.com</span>
        </li>
      </ul>
    </div>
    <div class="wordmark">
      <span class="wordmark__square"></span>
      <div>
        <span class="wordmark__name">HALVERN</span>
        <span class="wordmark__sub">CONTRACTING, INC.</span>
      </div>
    </div>
  </section>

</body>
</html>
```